Redesign of business card for Cedar Ridge Mechanical

We are looking for a new design for our business cards for Cedar Ridge Mechanical. We are a plumbing & HVAC construction company, operating on the West Coast of Canada and USA. Logo attached.
Industry/Entity Type
Construction - Plumbing & HVAC
Contact Information for Business Card
Name, address, phone numbers, email, website address
Look and feel
Each slider illustrates characteristics of the customer's brand and the style your logo design should communicate.

```html
<!DOCTYPE html>
<html lang="en">
<head>
<meta charset="utf-8">
<title>Cedar Ridge Mechanical – Business Card</title>
<link href="https://fonts.googleapis.com/css2?family=Outfit:wght@400;500;600&display=swap" rel="stylesheet">
<style>
  :root {
    --page: #d9d9d9;
    --card: #ffffff;
    --ink: #111111;
    --muted: #555555;
    --grey-band: #8a8c8c;
  }
  * { margin: 0; padding: 0; box-sizing: border-box; }
  html, body { width: 1200px; height: 896px; overflow: hidden; }
  body {
    background: var(--page);
    font-family: "Outfit", sans-serif;
    color: var(--ink);
    position: relative;
  }
  .card {
    position: absolute;
    left: 334px;
    width: 527px;
    height: 301px;
    background: var(--card);
    border-radius: 22px;
    overflow: hidden;
  }
  .card--front { top: 126px; }
  .card--back { top: 475px; }

  .wordmark {
    display: flex;
    align-items: center;
    gap: 12px;
    font-weight: 600;
    color: var(--ink);
    text-transform: uppercase;
    letter-spacing: 0.02em;
  }
  .wordmark__square { background: var(--ink); flex: none; }

  .card--front .wordmark {
    position: absolute;
    left: 0; right: 0; top: 0; bottom: 0;
    justify-content: center;
    font-size: 28px;
  }
  .card--front .wordmark__square { width: 30px; height: 30px; }

  .card--back .wordmark {
    position: absolute;
    left: 64px;
    top: 116px;
    width: 210px;
    font-size: 20px;
    line-height: 1.15;
    gap: 10px;
  }
  .card--back .wordmark__square { width: 24px; height: 24px; }

  .divider {
    position: absolute;
    left: 295px;
    top: 67px;
    width: 1px;
    height: 167px;
    background: var(--ink);
  }
  .contact {
    position: absolute;
    left: 309px;
    top: 64px;
    font-size: 14px;
    line-height: 1.45;
    color: var(--ink);
  }
  .contact__name { font-size: 19px; font-weight: 600; line-height: 1.2; }
  .contact__title { color: var(--muted); font-size: 13.5px; margin-bottom: 10px; }
  .contact__address { margin-bottom: 10px; line-height: 1.5; }
  .contact__line { display: flex; align-items: center; gap: 6px; line-height: 1.5; }
  .contact__line svg { width: 11px; height: 11px; flex: none; }

  .footer-band {
    position: absolute;
    left: 0;
    bottom: 0;
    width: 100%;
    height: 54px;
    background: linear-gradient(to right, var(--grey-band), var(--ink) 55%);
  }
  .website {
    position: absolute;
    right: 46px;
    bottom: 18px;
    color: #ffffff;
    font-size: 14px;
  }
</style>
</head>
<body>

  <section class="card card--front">
    <div class="wordmark"><span class="wordmark__square"></span>Cedar Ridge Mechanical</div>
  </section>

  <section class="card card--back">
    <div class="footer-band" role="img" aria-label="Decorative grey and black wave band along the bottom edge"></div>

    <div class="wordmark"><span class="wordmark__square"></span>Cedar Ridge Mechanical</div>

    <div class="divider"></div>

    <div class="contact">
      <p class="contact__name">DANIEL HAYES</p>
      <p class="contact__title">Managing Director</p>
      <p class="contact__address">Your address, City<br>State, Zip 1234</p>
      <p class="contact__line">
        <svg viewBox="0 0 24 24"><path d="M6.6 10.8a15 15 0 0 0 6.6 6.6l2.2-2.2a1 1 0 0 1 1-.25 11.4 11.4 0 0 0 3.6.6 1 1 0 0 1 1 1V20a1 1 0 0 1-1 1A17 17 0 0 1 3 4a1 1 0 0 1 1-1h3.5a1 1 0 0 1 1 1c0 1.25.2 2.45.6 3.6a1 1 0 0 1-.25 1z" fill="currentColor"/></svg>
        123 456 789
      </p>
      <p class="contact__line">
        <svg viewBox="0 0 24 24"><rect x="6" y="2" width="12" height="20" rx="2" fill="none" stroke="currentColor" stroke-width="2.4"/><circle cx="12" cy="18" r="1.3" fill="currentColor"/></svg>
        123 456 789
      </p>
      <p class="contact__line">
        <svg viewBox="0 0 24 24"><rect x="2" y="5" width="20" height="14" rx="1.5" fill="currentColor"/><path d="M3 6l9 7 9-7" fill="none" stroke="#fff" stroke-width="1.8"/></svg>
        info@yourgmail.com
      </p>
    </div>

    <p class="website">www.yourwebsite.com</p>
  </section>

</body>
</html>
```